Modern design company business card design

We are a design oriented construction firm. The owner is an architect and licensed General Contractor and accomplished furniture designer. We do new home construction and large scale remodeling and office design. We would like a design for our new business cards that is clean and modern, but relatable. We like the bright green color of our logo mixed with different shades of grey. We're also open to reinterpreting the logo.

Target Market(s)

Potential design clients,
Construction clients

Industry/Entity Type

Architecture

Contact Information for Business Card

Tall Maple Design | Build Inc. (optional with logo, Inc. optional)Jeffrey MorganOwner (optional)317.555.0148 cell317.431.8056 officejmorgan@greensquareinc.comwww.greensquareinc.com

Font styles to use
Sans Serif
Other font styles liked:
• Avenir

Requirements
Nice to have
• I like designs that have some continuity between the front and back, i.e. similar layouts or graphic elements that wrap around the card. I tend to prefer horizontal over vertical, but that's not a have to. I also tend to prefer white or recycled paper.

```html
<!DOCTYPE html>
<html lang="en">
<head>
<meta charset="utf-8">
<title>Tall Maple Design | Build – Business Card</title>
<link rel="stylesheet" href="https://fonts.googleapis.com/css2?family=Open+Sans:wght@400;600;700&display=swap">
<style>
  :root {
    --green: #3fa83c;
    --green-light: #a8d86a;
    --grey-dark: #3c3d42;
    --grey-mid: #6b6c72;
    --grey-light: #9a9ba0;
    --ink: #3d3d3d;
    --paper: #ffffff;
    --stage: #ecece8;
  }
  * { margin: 0; padding: 0; box-sizing: border-box; }
  html, body { width: 1200px; height: 913px; overflow: hidden; }
  body {
    background: var(--stage);
    font-family: "Open Sans", Arial, sans-serif;
    display: flex;
    align-items: center;
    justify-content: center;
    gap: 60px;
  }
  .card {
    position: relative;
    width: 520px;
    height: 297px;
    border-radius: 14px;
    overflow: hidden;
    box-shadow: 0 6px 18px rgba(0,0,0,.18);
  }
  .card--front { background: var(--paper); }
  .card--back { background: linear-gradient(160deg, var(--grey-mid), var(--grey-dark)); }
  .card__art { position: absolute; inset: 0; width: 100%; height: 100%; }

  .brand {
    position: absolute;
    top: 22px;
    right: 24px;
    font-weight: 600;
    font-size: 14px;
    letter-spacing: 1.5px;
    line-height: 1;
    text-transform: uppercase;
    white-space: nowrap;
  }
  .card--front .brand { color: var(--grey-light); }
  .card--back .brand { color: #e4e4e4; }

  .holder {
    position: absolute;
    left: 0;
    top: 110px;
    width: 480px;
    display: flex;
  }
  .holder__tab { width: 12px; height: 34px; background: var(--green); }
  .holder__text { padding-left: 14px; }
  .holder__name {
    font-size: 18px;
    font-weight: 700;
    color: var(--ink);
    letter-spacing: .5px;
    text-transform: uppercase;
    line-height: 1.1;
    white-space: nowrap;
  }
  .holder__role { font-size: 12px; color: var(--green); font-weight: 600; }
  .holder__rule {
    position: absolute;
    left: 228px;
    right: 0;
    top: 12px;
    height: 1px;
    background: var(--green);
  }

  .contacts {
    position: absolute;
    left: 0;
    bottom: 30px;
    list-style: none;
  }
  .contacts li {
    display: flex;
    align-items: center;
    height: 17px;
    font-size: 12px;
    color: var(--ink);
    white-space: nowrap;
  }
  .contacts__icon {
    width: 28px;
    height: 14px;
    margin-right: 6px;
    background: var(--green);
    border-radius: 0 7px 7px 0;
    display: flex;
    align-items: center;
    justify-content: flex-end;
    padding-right: 4px;
  }
  .contacts__icon svg { width: 9px; height: 9px; fill: none; stroke: #fff; stroke-width: 1.6; }
</style>
</head>
<body>

<section class="card card--front" aria-label="Business card front">
  <svg class="card__art" viewBox="0 0 520 297" preserveAspectRatio="none" aria-hidden="true">
    <defs>
      <linearGradient id="frontGrey" x1="0" y1="0" x2="1" y2="1">
        <stop offset="0" stop-color="#8a8b90"/>
        <stop offset="1" stop-color="#3c3d42"/>
      </linearGradient>
    </defs>
    <path d="M250 297 C 320 270, 380 200, 430 172 L 520 168 L 520 297 Z" fill="url(#frontGrey)"/>
    <path d="M250 297 C 320 270, 380 200, 430 172" fill="none" stroke="var(--green)" stroke-width="5"/>
    <path d="M430 172 L 520 168" fill="none" stroke="var(--green)" stroke-width="2"/>
  </svg>

  <p class="brand">Tall Maple Design | Build</p>

  <div class="holder">
    <div class="holder__tab"></div>
    <div class="holder__text">
      <p class="holder__name">Dennis Holloway</p>
      <p class="holder__role">Owner</p>
    </div>
    <div class="holder__rule"></div>
  </div>

  <ul class="contacts">
    <li><span class="contacts__icon"><svg viewBox="0 0 10 10"><rect x="3" y="1" width="4" height="8" rx="1"/></svg></span>317.555.0172</li>
    <li><span class="contacts__icon"><svg viewBox="0 0 10 10"><path d="M2 1 L4 1 L5 3 L4 4 Q5 6 6 6 L7 5 L9 6 L9 8 Q5 9 2 5 Q1 3 2 1 Z"/></svg></span>317.555.0148</li>
    <li><span class="contacts__icon"><svg viewBox="0 0 10 10"><circle cx="5" cy="5" r="4"/><path d="M1 5 H9 M5 1 Q2 5 5 9 M5 1 Q8 5 5 9"/></svg></span>www.tallmapleinc.example</li>
    <li><span class="contacts__icon"><svg viewBox="0 0 10 10"><rect x="1" y="2" width="8" height="6"/><path d="M1 2 L5 6 L9 2"/></svg></span>dholloway@tallmapleinc.example</li>
  </ul>
</section>

<section class="card card--back" aria-label="Business card back">
  <svg class="card__art" viewBox="0 0 520 297" preserveAspectRatio="none" aria-hidden="true">
    <defs>
      <linearGradient id="backGreen" x1="0" y1="0" x2="1" y2="1">
        <stop offset="0" stop-color="#5cc24a"/>
        <stop offset="1" stop-color="#2b8a2e"/>
      </linearGradient>
    </defs>
    <path d="M250 297 C 320 270, 380 200, 430 172 L 520 168 L 520 297 Z" fill="url(#backGreen)"/>
    <path d="M250 297 C 320 270, 380 200, 430 172 L 520 168" fill="none" stroke="var(--green-light)" stroke-width="4"/>
  </svg>

  <p class="brand">Tall Maple Design | Build</p>
</section>

</body>
</html>
```